Event flyer for Sunday night Youth Group

Need a 4 x 6 or 5 x 7 flyer for a new youth group starting on April 14. The youth group is for students in middle school and high school so it needs to look fun and cool, but not childish. I prefer it not to include pictures of people unless it's so obscure you can't really see their faces. I've uploaded some pictures of flyers I like. I've also attached a couple versions of our logo to use on the flyer.
Information the flyer needs to include:
Youth Group
Sundays, 6-8pm (beginning April 14)
Location: Marlowe's - 4219 Quarry Fern Ave N, Brayton, 97318
There will be dinner, games, friends, and a message.
Target Market(s)
Youth ages 13-18
Industry/Entity Type
Church
Font styles to use
Colors
Designer to choose colors to be used in the design.
Look and feel

```html
<!DOCTYPE html>
<html lang="en">
<head>
<meta charset="utf-8">
<title>Youth Group Flyer</title>
<link rel="stylesheet" href="https://fonts.googleapis.com/css2?family=Kaushan+Script&family=Montserrat:wght@500&family=Poppins:wght@400;600;700;800&display=swap">
<style>
  :root {
    --page-bg: #c4c4c4;
    --ink-black: #0b0b0c;
    --ink-white: #ffffff;
    --logo-grey: #d9d6d2;
    --glow-core: #f6e2b8;
    --glow-warm: #a66a32;
    --glow-deep: #4a2b14;
    --rule-bronze: #8a4a1c;
    --accent-blue: #14a6f0;
    --accent-cyan: #16dcf4;
    --chip-text: #0a1b3c;
    --pin-red: #e3162b;
  }
  * { margin: 0; padding: 0; box-sizing: border-box; }
  html, body {
    width: 1200px;
    height: 2400px;
    overflow: hidden;
    background: var(--page-bg);
  }
  .flyer {
    position: absolute;
    left: 100px;
    top: 500px;
    width: 1000px;
    height: 1400px;
    overflow: hidden;
    background: var(--ink-black);
    box-shadow: 0 8px 18px rgba(0,0,0,0.35);
    font-family: "Poppins", sans-serif;
  }
  .flyer__photo {
    position: absolute;
    inset: 0;
    background:
      radial-gradient(ellipse 45% 28% at 50% 22%, var(--glow-core) 0%, rgba(214,160,90,0.75) 30%, rgba(120,72,34,0) 100%),
      radial-gradient(ellipse 90% 55% at 50% 35%, var(--glow-warm) 0%, var(--glow-deep) 55%, rgba(20,12,8,0.9) 85%),
      linear-gradient(to bottom, #3a2414 0%, #5a3618 40%, #2a1a10 62%, var(--ink-black) 80%);
  }
  .brand {
    position: absolute;
    top: 82px;
    left: 0;
    width: 100%;
    display: flex;
    justify-content: center;
    align-items: center;
    gap: 22px;
  }
  .brand__mark {
    width: 22px;
    height: 22px;
    background: var(--logo-grey);
  }
  .brand__name {
    font-family: "Montserrat", sans-serif;
    font-weight: 500;
    color: var(--logo-grey);
    text-align: center;
    line-height: 1.05;
  }
  .brand__name .line1 { display: block; font-size: 44px; letter-spacing: 1px; }
  .brand__name .line2 { display: block; font-size: 24px; letter-spacing: 9px; }
  .title-rule {
    position: absolute;
    left: 189px;
    width: 604px;
    height: 3px;
    background: linear-gradient(to right, rgba(138,74,28,0), var(--rule-bronze) 15%, #c37a2e 50%, var(--rule-bronze) 85%, rgba(138,74,28,0));
  }
  .title-rule--top { top: 404px; }
  .title-rule--bottom { top: 554px; }
  .title-script {
    position: absolute;
    top: 200px;
    left: 0;
    width: 100%;
    text-align: center;
    font-family: "Kaushan Script", cursive;
    font-size: 268px;
    line-height: 1;
    color: var(--ink-black);
    z-index: 2;
    padding-right: 20px;
  }
  .title-block {
    position: absolute;
    top: 392px;
    left: 0;
    width: 100%;
    text-align: center;
    font-weight: 800;
    font-size: 178px;
    line-height: 1;
    letter-spacing: -2px;
    color: var(--ink-white);
    z-index: 1;
    padding-left: 30px;
  }
  .schedule {
    position: absolute;
    top: 1026px;
    left: 0;
    width: 100%;
    text-align: center;
    font-weight: 600;
    font-size: 68px;
    line-height: 1;
    color: var(--ink-white);
    padding-right: 45px;
  }
  .schedule__time { color: var(--accent-cyan); font-weight: 600; }
  .schedule-rule {
    position: absolute;
    top: 1095px;
    left: 149px;
    width: 694px;
    height: 2px;
    background: var(--accent-cyan);
  }
  .start-date {
    position: absolute;
    top: 1100px;
    left: 0;
    width: 100%;
    text-align: center;
    font-size: 38px;
    letter-spacing: 7px;
    color: var(--ink-white);
    padding-right: 40px;
  }
  .location {
    position: absolute;
    top: 1168px;
    left: 70px;
    width: 860px;
    height: 56px;
    background: var(--accent-blue);
    transform: skewX(-22deg);
  }
  .location__content {
    position: absolute;
    top: 1168px;
    left: 90px;
    width: 860px;
    height: 56px;
    display: flex;
    align-items: center;
    gap: 24px;
    padding-left: 28px;
  }
  .location__pin { width: 30px; height: 40px; }
  .location__text {
    font-weight: 700;
    font-size: 28px;
    color: var(--ink-white);
    white-space: nowrap;
  }
  .extras-label {
    position: absolute;
    top: 1242px;
    left: 0;
    width: 100%;
    text-align: center;
    font-size: 24px;
    letter-spacing: 8px;
    color: var(--ink-white);
  }
  .extras {
    position: absolute;
    top: 1293px;
    left: 92px;
    width: 836px;
    height: 44px;
    display: flex;
    gap: 8px;
    list-style: none;
  }
  .extras__chip {
    flex: 1;
    display: flex;
    align-items: center;
    justify-content: center;
    transform: skewX(-20deg);
    font-weight: 700;
    font-size: 30px;
    color: var(--chip-text);
  }
  .extras__chip span { transform: skewX(20deg); }
  .extras__chip--blue { background: var(--accent-blue); }
  .extras__chip--cyan { background: var(--accent-cyan); }
</style>
</head>
<body>
  <main class="flyer">
    <div class="flyer__photo" role="img" aria-label="Warm golden stage light glowing over a dark crowd with raised hands in silhouette"></div>

    <div class="brand">
      <div class="brand__mark"></div>
      <div class="brand__name">
        <span class="line1">HARBORLINE</span>
        <span class="line2">FELLOWSHIP</span>
      </div>
    </div>

    <div class="title-rule title-rule--top"></div>
    <div class="title-rule title-rule--bottom"></div>
    <h1>
      <span class="title-script">Youth</span>
      <span class="title-block">GROUP</span>
    </h1>

    <p class="schedule">SUNDAYS : <span class="schedule__time">6-8PM</span></p>
    <div class="schedule-rule"></div>
    <p class="start-date">(Beginning April 14)</p>

    <div class="location"></div>
    <div class="location__content">
      <svg class="location__pin" viewBox="0 0 30 40" aria-hidden="true">
        <path d="M15 1C7.3 1 2 6.6 2 13.6 2 23 15 39 15 39s13-16 13-25.4C28 6.6 22.7 1 15 1z" fill="var(--pin-red)"/>
        <circle cx="15" cy="13.5" r="5.5" fill="var(--accent-blue)"/>
      </svg>
      <span class="location__text">Marlowe's - 4219 Quarry Fern Ave N, Brayton, 97318</span>
    </div>

    <p class="extras-label">THERE WILL BE</p>
    <ul class="extras">
      <li class="extras__chip extras__chip--blue"><span>DINNER</span></li>
      <li class="extras__chip extras__chip--cyan"><span>GAMES</span></li>
      <li class="extras__chip extras__chip--blue"><span>FRIENDS</span></li>
      <li class="extras__chip extras__chip--cyan"><span>A MESSAGE</span></li>
    </ul>
  </main>
</body>
</html>
```